Website Home Page for Women's Health Medical Office

Redesign existing homepage for website using existing logo. Current website location is www.meadowcrestwomens.com. Please give it a modern, streamlined, playful feel.

Please give it a feminine feel and make it bright and cheerful using logo colors.

Target Market(s)

Women between the ages of 25-45

Industry/Entity Type

Medical Office

Coding

Coded - Design and coding required

Number of Pages Required

1 page

Font styles to use
Sans Serif
Other font styles liked:
• SEGOI UI script for text and GIL SANS for bold (or their equivilent)

Colors
E54698
E96AAD
F1A4CE
F9D9EA
FCEFF6

Requirements
Must have
• Existing logo. Logo Colors. Feminine, cheerful, simple design. all relevant contact information
Nice to have
• clean lines and streamlined look
Should not have
• Cluttered

```html
<!DOCTYPE html>
<html lang="en">
<head>
<meta charset="utf-8">
<title>Meadowcrest OB/GYN – Home</title>
<link rel="stylesheet" href="https://fonts.googleapis.com/css2?family=Montserrat:wght@600;700&family=Source+Sans+3:wght@400;600&family=Oswald:wght@500&family=Yellowtail&display=swap">
<style>
:root{
  --pink:#ee2a8b;
  --pink-soft:#f1a4ce;
  --pink-pale:#fceff6;
  --teal:#1aa1a8;
  --ink:#2a2a2a;
  --body:#555;
  --grey-bg:#f5f5f5;
  --white:#fff;
}
*{box-sizing:border-box;margin:0;padding:0}
html,body{width:1200px;height:3218px;overflow:hidden;background:var(--white)}
body{position:relative;font-family:"Source Sans 3",sans-serif;color:var(--body)}
.abs{position:absolute}
a{text-decoration:none;color:inherit}

/* header */
.topline{left:0;top:0;width:1200px;height:4px;background:var(--teal)}
.site-header{left:0;top:4px;width:1200px;height:92px;background:var(--white)}
.brand{left:110px;top:30px;display:flex;align-items:center;gap:10px;font-family:"Montserrat",sans-serif;font-weight:700;font-size:19px;color:var(--ink)}
.brand-dot{width:30px;height:30px;border-radius:50%;background:var(--pink)}
.nav{top:41px;font-family:"Montserrat",sans-serif;font-weight:600;font-size:12.5px;color:var(--ink);text-transform:uppercase}
.nav.active{color:var(--pink)}
.nav.active::after{content:"";position:absolute;left:0;right:0;top:24px;height:3px;border-radius:2px;background:var(--pink)}
.btn{display:flex;align-items:center;justify-content:center;border:2.5px solid var(--pink);border-radius:30px;color:var(--pink);font-family:"Source Sans 3",sans-serif;font-weight:600;font-size:15px;text-transform:uppercase;background:transparent}
.quote-btn{left:935px;top:27px;width:153px;height:41px}

/* hero */
.hero{left:0;top:96px;width:1200px;height:680px;background:linear-gradient(100deg,#f3f3f3 0%,#ececec 45%,#e4e4e4 100%)}
.hero-title{left:106px;top:262px;font-family:"Montserrat",sans-serif;font-weight:700;font-size:55px;color:var(--ink)}
.hero-text{left:106px;top:334px;width:470px;font-size:13.5px;line-height:24px;color:#555}
.hero-btn{left:109px;top:434px;width:164px;height:48px}
.hero-art{left:0;top:96px}

/* help */
.section-title{font-family:"Montserrat",sans-serif;font-weight:700;font-size:41px;color:var(--ink);text-align:center}
.section-title .mark{background:linear-gradient(transparent 62%,var(--pink-soft) 62%,var(--pink-soft) 78%,transparent 78%)}
.help-title{left:0;top:742px;width:1200px}
.card{top:820px;width:232px;height:290px;text-align:center}
.card.featured{background:var(--white);box-shadow:0 4px 18px rgba(0,0,0,.10)}
.card-icon{margin:29px auto 0;width:90px;height:90px;border:2.5px solid var(--pink);border-radius:50%;display:flex;align-items:center;justify-content:center}
.card-title{margin-top:13px;font-family:"Source Sans 3",sans-serif;font-weight:600;font-size:21px;color:var(--ink)}
.card-text{margin:10px auto 0;width:180px;font-size:13.5px;line-height:21.5px;color:#666}
.learn{margin-top:14px;font-weight:600;font-size:13px;color:var(--pink);display:flex;align-items:center;justify-content:center;gap:6px}
.learn i{width:12px;height:12px;border-radius:50%;background:var(--pink);display:inline-block;position:relative}
.learn i::after{content:"";position:absolute;left:3px;top:3.5px;width:4px;height:4px;border-top:1.6px solid #fff;border-right:1.6px solid #fff;transform:rotate(45deg)}

/* serving */
.serving-art{left:0;top:1200px}
.serving-title{left:511px;top:1246px;width:560px;font-family:"Montserrat",sans-serif;font-weight:700;font-size:40px;line-height:48px;color:var(--white)}
.serving-text{left:511px;top:1358px;width:516px;font-size:12.3px;line-height:21.5px;color:var(--white)}
.serving-text p+p{margin-top:21.5px}

/* banner */
.banner{left:0;top:1725px;width:1200px;height:364px;background:linear-gradient(90deg,#efeeec,#f4f1ee 50%,#ececea)}
.banner-script{left:0;top:1816px;width:1200px;text-align:center;font-family:"Yellowtail",cursive;font-size:34px;color:var(--pink)}
.banner-title{left:0;top:1864px;width:1200px}
.banner-btn{left:496px;top:1930px;width:209px;height:47px}

/* specialists */
.spec-title{left:111px;top:2168px;text-align:left}
.spec-text{left:111px;top:2242px;width:478px;font-size:13.5px;line-height:24px;color:#555;text-align:justify}
.spec-text p+p{margin-top:24px}
.spec-photo{left:627px;top:2189px}

/* footer */
.footer-art{left:0;top:2700px}
.footer-head{top:2895px;font-family:"Oswald",sans-serif;font-weight:500;font-size:25px;color:var(--ink)}
.contact{left:113px;display:flex;align-items:flex-start;gap:16px;font-size:14.5px;line-height:25px;color:#333}
.contact-icon{width:42px;height:42px;border:2px solid #7a4f9c;border-radius:50%;display:flex;align-items:center;justify-content:center;flex:none;background:var(--white)}
.links{top:2945px;list-style:none;font-size:14.5px;line-height:25.6px;color:#333}
.links li::before{content:"»";display:inline-block;width:34px;padding-left:4px;font-size:14px}
.footer-brand{left:874px;top:2940px;width:215px;display:flex;flex-direction:column;align-items:center;gap:14px;font-family:"Montserrat",sans-serif;font-weight:700;font-size:22px;color:var(--ink);text-align:center}
.footer-brand .brand-dot{width:60px;height:60px}
.footer-rule{left:110px;top:3135px;width:979px;height:1px;background:#d0d0d0}
.copyright{left:0;top:3162px;width:1200px;text-align:center;font-size:13.5px;color:#333}
.code{left:1126px;top:3162px;font-size:12px;color:#444}
</style>
</head>
<body>

<div class="abs topline"></div>
<header class="abs site-header"></header>
<a class="abs brand" href="#"><span class="brand-dot"></span>Meadowcrest OB/GYN</a>
<nav>
  <a class="abs nav active" style="left:507px" href="#">Home</a>
  <a class="abs nav" style="left:569px" href="#">About Us</a>
  <a class="abs nav" style="left:655px" href="#">Services</a>
  <a class="abs nav" style="left:734px" href="#">Resources</a>
  <a class="abs nav" style="left:828px" href="#">Contact Us</a>
</nav>
<a class="abs btn quote-btn" href="#">Get a Quote</a>

<!-- hero -->
<section class="abs hero"></section>
<svg class="abs hero-art" width="1200" height="690" viewBox="0 96 1200 690">
  <defs>
    <linearGradient id="heroPhoto" x1="0" y1="0" x2="1" y2="1">
      <stop offset="0" stop-color="#d9c2b4"/>
      <stop offset=".5" stop-color="#b9c0cc"/>
      <stop offset="1" stop-color="#e9dcd6"/>
    </linearGradient>
  </defs>
  <circle cx="845" cy="600" r="350" fill="var(--pink)"/>
  <path role="img" aria-label="Photo: a doctor with a clipboard talking with a smiling young woman patient" d="M560 250 Q640 150 760 170 L900 150 Q1050 150 1140 300 L1200 420 V700 H620 Q560 560 560 420 Z" fill="url(#heroPhoto)" opacity=".9"/>
  <path d="M0 745 Q600 600 1200 722 V768 Q600 650 0 768 Z" fill="var(--pink)"/>
  <path d="M0 768 Q600 650 1200 768 V786 H0 Z" fill="var(--white)"/>
  <path d="M0 768 Q600 668 1200 742 V786 H0Z" fill="var(--white)" opacity="0"/>
</svg>
<h1 class="abs hero-title">Meadowcrest OB/GYN</h1>
<p class="abs hero-text">Meadowcrest OB/GYN in Briarwood, California, was formed in October of 2005 by Dr. Alan Whitford and Dr. Mira Castell, to help serve the great need for women’s health services in the Southern Valley region.</p>
<a class="abs btn hero-btn" href="#">Contact Us</a>

<!-- help -->
<h2 class="abs section-title help-title"><span class="mark">How Can We Help You?</span></h2>

<article class="abs card" style="left:111px">
  <div class="card-icon"><svg width="42" height="42" viewBox="0 0 42 42" fill="none" stroke="#222" stroke-width="2"><path d="M21 34 C8 25 6 17 11 12 C15 8 19 10 21 14 C23 10 27 8 31 12 C36 17 34 25 21 34Z"/></svg></div>
  <h3 class="card-title">Pregnancy Care</h3>
  <p class="card-text">Receiving regular care in pregnancy is important for the health of both</p>
  <a class="learn" href="#">LEARN MORE <i></i></a>
</article>
<article class="abs card featured" style="left:359px">
  <div class="card-icon"><svg width="42" height="42" viewBox="0 0 42 42" fill="none" stroke="#222" stroke-width="2"><rect x="8" y="15" width="26" height="12" rx="6" transform="rotate(-30 21 21)"/><line x1="17" y1="14" x2="23" y2="26"/></svg></div>
  <h3 class="card-title">Birth Control</h3>
  <p class="card-text">Our gynecologists are knowledgeable on all forms of birth control</p>
  <a class="learn" href="#">LEARN MORE <i></i></a>
</article>
<article class="abs card" style="left:608px">
  <div class="card-icon"><svg width="42" height="42" viewBox="0 0 42 42" fill="none" stroke="#222" stroke-width="2"><circle cx="21" cy="14" r="7"/><path d="M8 36 C8 27 14 23 21 23 C28 23 34 27 34 36Z"/></svg></div>
  <h3 class="card-title">Well Woman Exams</h3>
  <p class="card-text">Our providers will help you to stay healthy by performing a physical exam</p>
  <a class="learn" href="#">LEARN MORE <i></i></a>
</article>
<article class="abs card" style="left:856px">
  <div class="card-icon"><svg width="42" height="42" viewBox="0 0 42 42" fill="none" stroke="#222" stroke-width="2"><path d="M21 30 C10 22 8 15 12 11 C15 8 19 9 21 12 C23 9 27 8 30 11 C34 15 32 22 21 30Z"/><path d="M21 14 V22 M17 18 H25"/><path d="M4 26 L12 36 H18 M38 26 L30 36 H24"/></svg></div>
  <h3 class="card-title">Women's Health</h3>
  <p class="card-text">Whether you are dealing with painful or irregular periods, fibroids</p>
  <a class="learn" href="#">LEARN MORE <i></i></a>
</article>

<!-- serving -->
<svg class="abs serving-art" width="1200" height="480" viewBox="0 1200 1200 480">
  <defs>
    <radialGradient id="docPhoto" cx=".5" cy=".45" r=".6">
      <stop offset="0" stop-color="#7d7f90"/>
      <stop offset="1" stop-color="#2e3550"/>
    </radialGradient>
  </defs>
  <path d="M205 1325 A190 190 0 0 1 435 1241" fill="none" stroke="var(--pink)" stroke-width="16"/>
  <path d="M234 1357 A150 150 0 0 1 409 1275" fill="none" stroke="#333" stroke-width="14"/>
  <path d="M560 1229 H1089 V1496 A100 100 0 0 1 989 1596 H440 L390 1330 Q440 1229 560 1229 Z" fill="var(--pink)"/>
  <circle cx="295" cy="1486" r="192" fill="var(--white)"/>
  <circle role="img" aria-label="Portrait photo of a smiling doctor in navy scrubs" cx="295" cy="1486" r="184" fill="url(#docPhoto)"/>
</svg>
<h2 class="abs serving-title">Serving Meadowcrest Valley Medical Center</h2>
<div class="abs serving-text">
  <p>At Meadowcrest OB/GYN in Briarwood, California, we believe better health starts when the patient is educated. For this reason, we take time to listen to our patients concerns, explain each option available, and to answer any questions our patients may have so that they can make informed decisions. At Meadowcrest OB/GYN, our providers tailor every procedure performed and treatment option recommended to meet the specific needs of our patients. We remain up-to-date on the latest technology and practice guidelines for women’s health.</p>
  <p>Our medical providers will take time to give you the personalized health care you deserve. This includes taking time to listen to you and screening you for problems to help ensure that any health issues are diagnosed and treated as early as possible.</p>
</div>

<!-- banner -->
<section class="abs banner" role="img" aria-label="Faded photo of a nurse caring for a mother and newborn"></section>
<p class="abs banner-script">Better Health Starts Here!</p>
<h2 class="abs section-title banner-title">Now Accepting New Patients</h2>
<a class="abs btn banner-btn" href="#">Book an Appointment</a>

<!-- specialists -->
<h2 class="abs section-title spec-title"><span class="mark">Your Ob/gyn Specialists</span></h2>
<div class="abs spec-text">
  <p>Meadowcrest OB/GYN offers you the best care possible in a personalized setting. We are currently accepting patients. Call our office now to make an appointment.</p>
  <p>Meadowcrest OB/GYN (located near Valley Springs Hospital in Briarwood, CA) is a medical office that specializes in Christ-centered healthcare for women of all ages. Our team of exclusively female providers have years of experience taking care of women with a variety of pregnancy and gynecology concerns.</p>
  <p>Whether you need a routine examination, help during your pregnancy, have questions on birth control, or another female concern, we offer the best care possible for our patients. That is why better health starts here.</p>
  <p>Our office provides you with an environment where you can feel comfortable and where you know you will be in good hands. Our providers are leaders women’s health. Dr. Castell is a board certified obstetrician and gynecologist. Dr. Navarre is a board eligible obstetrician and gynecologist.</p>
</div>
<svg class="abs spec-photo" width="460" height="453" viewBox="0 0 460 453">
  <defs>
    <linearGradient id="specPhoto" x1="0" y1="0" x2="1" y2="1">
      <stop offset="0" stop-color="#b9cbe0"/>
      <stop offset=".55" stop-color="#efe6dc"/>
      <stop offset="1" stop-color="#f6f2ee"/>
    </linearGradient>
  </defs>
  <path role="img" aria-label="Photo of a nurse with a mother holding her newborn baby" d="M120 0 H340 A120 120 0 0 1 460 120 V453 H120 A120 120 0 0 1 0 333 V120 A120 120 0 0 1 120 0 Z" fill="url(#specPhoto)"/>
</svg>

<!-- footer -->
<svg class="abs footer-art" width="1200" height="518" viewBox="0 2700 1200 518">
  <rect x="0" y="2716" width="1200" height="502" fill="var(--grey-bg)"/>
  <path d="M0 2716 H1200 V2742 Q600 2900 0 2744 Z" fill="var(--pink)"/>
  <path d="M0 2700 H1200 V2722 Q600 2878 0 2722 Z" fill="var(--white)"/>
</svg>

<h4 class="abs footer-head" style="left:110px">CONNECT</h4>
<div class="abs contact" style="top:2940px">
  <span class="contact-icon"><svg width="14" height="16" viewBox="0 0 14 16"><path d="M7 1 C3.5 1 1.5 3.5 1.5 6 C1.5 9.5 7 15 7 15 C7 15 12.5 9.5 12.5 6 C12.5 3.5 10.5 1 7 1Z" fill="#7a4f9c"/><circle cx="7" cy="6" r="2" fill="#fff"/></svg></span>
  <span>Lorem ipsum dolor sit amet,<br>consectetur adipiscing</span>
</div>
<div class="abs contact" style="top:3014px">
  <span class="contact-icon"><svg width="14" height="14" viewBox="0 0 14 14"><path d="M3 1 L5.5 1.5 L6 4.5 L4.5 5.5 C5.3 7.3 6.7 8.7 8.5 9.5 L9.5 8 L12.5 8.5 L13 11 C13 12 12 13 11 13 C5.5 13 1 8.5 1 3 C1 2 2 1 3 1Z" fill="#7a4f9c"/></svg></span>
  <span style="line-height:42px">+1 888 888 8888</span>
</div>
<div class="abs contact" style="top:3066px">
  <span class="contact-icon"><svg width="15" height="12" viewBox="0 0 15 12"><rect x="0.5" y="1" width="14" height="10" rx="1" fill="#7a4f9c"/><path d="M1 2 L7.5 7 L14 2" fill="none" stroke="#fff" stroke-width="1.3"/></svg></span>
  <span style="line-height:42px">info@companyname.com</span>
</div>

<h4 class="abs footer-head" style="left:482px">EXPLORE</h4>
<ul class="abs links" style="left:482px">
  <li>Courses</li><li>Blog</li><li>My Library</li><li>Store</li><li>Privacy</li>
</ul>

<h4 class="abs footer-head" style="left:667px">RESOURCES</h4>
<ul class="abs links" style="left:667px">
  <li>Home</li><li>Sections Guide</li><li>Tutorials</li><li>Contact Us</li><li>Support</li>
</ul>

<div class="abs footer-brand"><span class="brand-dot"></span>Meadowcrest OB/GYN</div>

<div class="abs footer-rule"></div>
<p class="abs copyright">© 2022 LRK Health | All Rights Reserved</p>
<p class="abs code">C38</p>

</body>
</html>
```